Keystone Trench Co Business Card*

Looking for a professional, clean and crisp business card

I am in the underground utilities industry and am just looking for a really impressive business card. I would like our card to be white with our symbol crisp and clear with it protruding. I also have a business partner that will require his name and info on the card once the design is set. I would like to have our website info on the card which is;
http://keystonetrenchco.example/

Contact Information for Business Card

Website, contact name, number and email

```html
<!DOCTYPE html>
<html lang="en">
<head>
<meta charset="utf-8">
<title>Keystone Trench Co Business Card</title>
<link href="https://fonts.googleapis.com/css2?family=Roboto+Condensed:wght@400;700&display=swap" rel="stylesheet">
<style>
  :root {
    --backdrop: #b9b9b9;
    --card-white: #ffffff;
    --card-black: #231f20;
    --brand-blue: #3a62a8;
    --ink: #231f20;
    --icon-red: #e5202a;
    --paper-white: #ffffff;
  }
  * { margin: 0; padding: 0; box-sizing: border-box; }
  html, body {
    width: 1200px; height: 801px; overflow: hidden;
    background: var(--backdrop);
    font-family: "Roboto Condensed", "Arial Narrow", sans-serif;
  }
  .canvas { position: relative; width: 1200px; height: 801px; }

  .card {
    position: absolute; top: 274px;
    width: 443px; height: 263px; overflow: hidden;
  }
  .card--front { left: 153px; background: var(--card-white); }
  .card--back { left: 625px; background: var(--card-black); }

  .front__band {
    position: absolute; left: 68px; top: 0;
    width: 56px; height: 100%;
    background: var(--brand-blue);
  }
  .brand-mark {
    position: absolute; border-radius: 50%;
    display: flex; align-items: center; justify-content: center;
    text-align: center;
    font-weight: 700; text-transform: uppercase; line-height: 1.05;
  }
  .card--front .brand-mark {
    left: 27px; top: 62px; width: 140px; height: 140px;
    background: var(--card-white);
    border: 4px solid var(--ink);
    color: var(--ink); font-size: 21px;
  }
  .card--back .brand-mark {
    left: 164px; top: 53px; width: 114px; height: 114px;
    border: 3px solid var(--paper-white);
    color: var(--paper-white); font-size: 17px;
  }

  .contact { position: absolute; left: 211px; top: 78px; color: var(--ink); }
  .contact__name { font-size: 18px; font-weight: 700; letter-spacing: 0.2px; line-height: 1; }
  .contact__role { font-size: 14px; line-height: 1.15; margin-top: 1px; }
  .contact__list { list-style: none; margin-top: 22px; }
  .contact__item {
    display: flex; align-items: center; gap: 4px;
    font-size: 14px; line-height: 16.5px;
  }
  .contact__icon { width: 13px; height: 13px; flex: none; }

  .back__band {
    position: absolute; left: 0; top: 204px;
    width: 100%; height: 31px;
    background: var(--brand-blue);
    color: var(--paper-white);
    display: flex; align-items: center; justify-content: center;
    font-size: 14px; letter-spacing: 0.4px;
  }
</style>
</head>
<body>
<main class="canvas">
  <section class="card card--front" aria-label="Card front">
    <div class="front__band"></div>
    <div class="brand-mark">Keystone<br>Trench Co</div>

    <div class="contact">
      <h1 class="contact__name">DANIEL HARPER</h1>
      <p class="contact__role">Managing Director</p>
      <ul class="contact__list">
        <li class="contact__item">
          <svg class="contact__icon" viewBox="0 0 24 24" aria-hidden="true"><path fill="var(--icon-red)" d="M6.6 10.8a15.1 15.1 0 0 0 6.6 6.6l2.2-2.2c.3-.3.7-.4 1-.2 1.1.4 2.3.6 3.6.6.6 0 1 .4 1 1V20c0 .6-.4 1-1 1A17 17 0 0 1 3 4c0-.6.4-1 1-1h3.5c.6 0 1 .4 1 1 0 1.3.2 2.5.6 3.6.1.3 0 .7-.2 1z"/></svg>
          044-555 010 237
        </li>
        <li class="contact__item">
          <svg class="contact__icon" viewBox="0 0 24 24" aria-hidden="true"><rect x="2" y="5" width="20" height="14" fill="var(--icon-red)"/><path d="M2 5l10 8 10-8" fill="none" stroke="#fff" stroke-width="1.6"/></svg>
          hello@keystonetrenchco.example
        </li>
        <li class="contact__item">
          <svg class="contact__icon" viewBox="0 0 24 24" aria-hidden="true"><g fill="none" stroke="var(--icon-red)" stroke-width="2"><circle cx="12" cy="12" r="10"/><ellipse cx="12" cy="12" rx="4.5" ry="10"/><path d="M2 12h20M4 7h16M4 17h16"/></g></svg>
          www.keystonetrenchco.example
        </li>
      </ul>
    </div>
  </section>

  <section class="card card--back" aria-label="Card back">
    <div class="brand-mark">Keystone<br>Trench Co</div>
    <div class="back__band">www.keystonetrenchco.example</div>
  </section>
</main>
</body>
</html>
```